K & R Acre Works. Business card design

We need a business card designed for a new business. We have a bulldozer and tractor service. We clear land and make wildlife food plots. We provide disking, bush hogging, and site prep services.
I have attached an image of a business card that I like and would like my business cards to look similar.

Target Market(s)

anyone needing bulldozer and/or tractor services

Industry/Entity Type

Business

Contact Information for Business Card

K & R Acre Works, Operated by 7-T-Ranch
Wade Colton
601-472-3358
wcr4817@fieldmail-example.com

Font styles to use
Sans Serif

Colors

Designer to choose colors to be used in the design.

Requirements
Must have
• image of tractor and bulldozer
• Land Clearing
• Wildlife food plots
• Bush Hogging
• Disking
• Site prep
Nice to have
• i have included a image of a business card that i like. I would like mine to be similar.

```html
<!DOCTYPE html>
<html lang="en">
<head>
<meta charset="utf-8">
<title>K &amp; R Acre Works — Business Card</title>
<link rel="stylesheet" href="https://fonts.googleapis.com/css2?family=Bebas+Neue&family=Montserrat:wght@400&family=Roboto+Condensed:wght@400&display=swap">
<style>
  :root {
    --page-bg: #e9e4dc;
    --card-shadow: rgba(40, 28, 15, 0.35);
    --photo-green-dark: #1e2a17;
    --photo-green: #34452a;
    --photo-red: #8a2e1c;
    --photo-orange: #b5472a;
    --overlay: rgba(10, 12, 8, 0.55);
    --text: #ffffff;
    --rule: #ffffff;
  }
  * { box-sizing: border-box; margin: 0; padding: 0; }
  html, body {
    width: 1200px;
    height: 930px;
    overflow: hidden;
    background: var(--page-bg);
  }
  .card {
    position: absolute;
    left: 100px;
    top: 180px;
    width: 1000px;
    height: 570px;
    border-radius: 27px;
    overflow: hidden;
    box-shadow: 0 14px 36px var(--card-shadow);
    color: var(--text);
  }
  .card__photo {
    position: absolute;
    inset: 0;
    background:
      radial-gradient(ellipse 45% 50% at 38% 62%, var(--photo-orange) 0%, var(--photo-red) 45%, transparent 80%),
      radial-gradient(ellipse 30% 35% at 72% 70%, var(--photo-red) 0%, transparent 75%),
      linear-gradient(180deg, var(--photo-green) 0%, var(--photo-green-dark) 55%, #2c2a1c 100%);
  }
  .card__overlay {
    position: absolute;
    inset: 0;
    background: var(--overlay);
  }
  .brand {
    position: absolute;
    left: 71px;
    top: 246px;
  }
  .brand__name {
    font-family: "Bebas Neue", sans-serif;
    font-size: 49px;
    line-height: 1;
    letter-spacing: 0.5px;
  }
  .brand__operator {
    font-family: "Montserrat", sans-serif;
    font-size: 19px;
    letter-spacing: 6px;
    margin-top: 4px;
    text-transform: uppercase;
  }
  .divider {
    position: absolute;
    left: 546px;
    top: 116px;
    width: 3px;
    height: 335px;
    background: var(--rule);
  }
  .contact {
    position: absolute;
    left: 592px;
    top: 108px;
  }
  .contact__name {
    font-family: "Bebas Neue", sans-serif;
    font-size: 72px;
    line-height: 1;
    letter-spacing: 0.5px;
  }
  .contact__line {
    display: flex;
    align-items: center;
    gap: 16px;
    font-family: "Roboto Condensed", sans-serif;
    font-size: 32px;
    line-height: 42px;
  }
  .contact__line svg { width: 24px; height: 24px; flex: none; }
  .contact__line:first-of-type { margin-top: 6px; }
  .services {
    list-style: none;
    margin-top: 22px;
    font-family: "Bebas Neue", sans-serif;
    font-size: 42px;
    line-height: 46px;
  }
</style>
</head>
<body>
  <article class="card">
    <div class="card__photo" role="img" aria-label="Photograph of a red tractor with front loader and a bulldozer on a cleared field with trees behind"></div>
    <div class="card__overlay"></div>

    <div class="brand">
      <div class="brand__name">K &amp; R Acre Works</div>
      <div class="brand__operator">Operated by 7-T-Ranch</div>
    </div>

    <div class="divider"></div>

    <div class="contact">
      <h1 class="contact__name">WADE COLTON</h1>
      <p class="contact__line">
        <svg viewBox="0 0 24 24" fill="none" stroke="currentColor" stroke-width="2" stroke-linecap="round" stroke-linejoin="round" aria-hidden="true">
          <path d="M7 3 L10 7 L8 9.5 C9 12.5 11.5 15 14.5 16 L17 14 L21 17 L19 20.5 C11 20 4 13 3.5 5 Z"/>
        </svg>
        601-472-3358
      </p>
      <p class="contact__line">
        <svg viewBox="0 0 24 24" fill="none" stroke="currentColor" stroke-width="2" stroke-linejoin="round" aria-hidden="true">
          <rect x="3" y="6" width="18" height="12" rx="1"/>
          <path d="M3 7 L12 13 L21 7"/>
        </svg>
        wcr4817@fieldmail-example.com
      </p>
      <ul class="services">
        <li>Land Clearing</li>
        <li>Wildlife Food Plots</li>
        <li>Bush Hogging</li>
        <li>Disking – Site Prep</li>
      </ul>
    </div>
  </article>
</body>
</html>
```